Modern, clean and professional Wordpress design for a safety training company!

We are currently in the process of creating a new website for our business. We have hired a website developer and the main structure of our new Wordpress site is complete. We now need an overall design plan for the site. We need a very clean, professional and easy to follow website. Most of our website visitors only spend about 30-45 secs on our sites "shopping " so it is imperative that we have a strong Home Page.
Our company specializes in CPR and First Aid Certification Classes to businesses and individuals throughout Northern California. We provide these certifications two ways: ONSITE-We come to you, and HOSTED-we offer weekly classes at our 2 locations.
Our design needs to use the general green and blue colors of our logo. But we also like white.
The final design MUST communicate a legitimate, trustworthy and professional business. Our industry is VERY competitive and we need to STAND OUT.
Currently, the NEW website that we need a new design for is www.LifelineDrillWorks.com
Our old website is www.RescuePrepValleyHub.com and we really do like the design of this website, but we just needed a Wordpress site for SEO purposes.
These are 3 websites that we really:
http://morvaliontech.com/
http://www.tralbex.com/
https://www.plivant.com/
I have attached our Logo and other images if you need to use them but looking at the current two sites will be you best help.
Target Market(s)
1) Large businesses and industries that are looking for a company to provide ONSITE safety training classes at their office or place of work.
2) Individuals that need certifications for their jobs and other needs. These individuals are looking for a legitimate, trustworthy and professional environment to complete their training class.

```html
<!DOCTYPE html>
<html lang="en">
<head>
<meta charset="utf-8">
<title>Keystone Rescue Academy</title>
<link href="https://fonts.googleapis.com/css2?family=Open+Sans:wght@400;600;700&display=swap" rel="stylesheet">
<style>
:root{
  --blue:#2b4a9b;
  --blue-dark:#1f3b85;
  --green:#a3c10c;
  --ink:#222;
  --text:#333;
  --page:#f1f1f1;
  --white:#fff;
  --dark:#333;
  --footer:#111;
}
*{box-sizing:border-box;margin:0;padding:0}
html,body{width:736px;height:1200px;overflow:hidden}
body{font-family:"Open Sans",Arial,sans-serif;background:var(--page);color:var(--text);position:relative}
.abs{position:absolute}
.header{top:0;left:0;width:736px;height:82px;background:#f4f4f4}
.brand{left:35px;top:20px;display:flex;align-items:center;gap:8px}
.brand-mark{width:14px;height:14px;border-radius:50%;background:var(--green)}
.brand-name{font-size:17px;font-weight:700;color:var(--blue);line-height:1.1}
.contact{top:30px;display:flex;align-items:center;gap:6px;font-size:8px;color:var(--ink)}
.contact .ic{width:24px;height:24px;border-radius:50%;background:var(--green);display:flex;align-items:center;justify-content:center}
.nav{top:82px;left:0;width:736px;height:28px;background:var(--blue);border-top:2px solid var(--blue-dark);display:flex;align-items:center;padding-left:58px;gap:25px}
.nav a{color:#fff;font-size:8.5px;font-weight:600;text-decoration:none;text-transform:uppercase}
.hero{top:110px;left:0;width:736px;height:288px;background:linear-gradient(180deg,#e8e4dc 0%,#b7a894 45%,#6e5a4a 100%)}
.tagline{top:274px;left:44px;height:34px;padding:0 6px;background:rgba(255,255,255,.55);font-size:17.5px;color:#111;line-height:34px}
.card{top:329px;width:202px;height:202px;background:#fff;border:1px solid #ddd;padding:18px 12px}
.card h2{font-size:18px;font-weight:400;color:var(--blue);padding-bottom:8px;border-bottom:1px solid #ccc;margin-bottom:14px}
.card p{font-size:6.8px;line-height:13.6px;color:#333;height:90px}
.card.green{background:var(--green);border-color:var(--green)}
.card.green h2{color:#111;border-color:#bcd44d}
.card.green p{color:#222}
.btn{display:inline-block;background:var(--dark);color:#fff;font-size:8.5px;font-weight:600;padding:7px 9px;margin-top:2px}
.news{top:562px;left:32px;width:436px;height:216px;background:#fff;padding:12px 11px}
.news h3{font-size:14px;font-weight:400;color:var(--blue);margin-bottom:10px}
.news-grid{display:flex;gap:21px}
.post{width:195px}
.post .ph{width:195px;height:103px}
.post h4{font-size:8.4px;font-weight:600;color:#111;margin-top:4px}
.post .date{font-size:7px;color:var(--green);margin-top:6px}
.post p{font-size:7px;line-height:16px;color:#222;margin-top:1px}
.price{left:490px;width:204px;height:98px;background:var(--blue);color:#fff;padding:8px 15px}
.price .t{font-size:16px;font-weight:600}
.price .t b{font-size:20px}
.price .row{display:flex;justify-content:space-between;font-size:8.5px;font-weight:600;margin-top:4px}
.price .row span:last-child{color:var(--green)}
.reg{display:inline-block;margin-top:9px;background:var(--green);color:#222;font-size:8.5px;padding:5px 13px}
.reviews{top:806px;left:32px;width:673px;height:115px;background:#fff;border-left:4px solid var(--green);padding:14px 27px}
.reviews h3{font-size:14px;font-weight:400;color:var(--blue)}
.stars{display:flex;gap:1px;margin:3px 0 5px -3px}
.reviews .who{font-size:10px;color:#111;font-weight:600}
.reviews .who span{color:var(--green);font-weight:400}
.reviews p{font-size:6.8px;line-height:16px;color:#222;margin-top:3px}
.map{top:945px;left:0;width:736px;height:149px;background:#e9e6df}
.footer{top:1094px;left:0;width:736px;height:106px;background:var(--footer)}
.social{top:1114px;left:284px;display:flex;gap:6px}
.social span{width:22px;height:22px;border:1.5px solid #ddd;border-radius:50%}
.flinks{top:1150px;left:0;width:736px;text-align:center;font-size:8px;color:#ddd}
.flinks i{font-style:normal;margin:0 7px;color:#aaa}
.copy{top:1168px;left:0;width:736px;text-align:center;font-size:8px;color:var(--green)}
.badge{top:1125px;left:676px;width:30px;height:48px;background:#fff;border-radius:2px}
</style>
</head>
<body>
<header class="abs header">
  <div class="abs brand"><span class="brand-mark"></span><span class="brand-name">Keystone Rescue<br>Academy</span></div>
  <div class="abs contact" style="left:434px">
    <span class="ic"><svg width="11" height="11" viewBox="0 0 24 24"><path fill="#222" d="M6.6 10.8a15 15 0 0 0 6.6 6.6l2.2-2.2a1 1 0 0 1 1-.25 11.4 11.4 0 0 0 3.6.57 1 1 0 0 1 1 1V20a1 1 0 0 1-1 1A17 17 0 0 1 3 4a1 1 0 0 1 1-1h3.5a1 1 0 0 1 1 1c0 1.25.2 2.45.57 3.57a1 1 0 0 1-.25 1z"/></svg></span>
    Call us : 916-555-0182
  </div>
  <div class="abs contact" style="left:566px">
    <span class="ic"><svg width="11" height="9" viewBox="0 0 22 16"><rect width="22" height="16" rx="2" fill="#222"/><path d="M1 1l10 8 10-8" stroke="#a3c10c" stroke-width="1.5" fill="none"/></svg></span>
    Email us : info@keystonerescue.com
  </div>
</header>

<nav class="abs nav">
  <a>Home</a><a>Class Calender</a><a>Classes for Groups</a><a>Certification Classes</a><a>About Us</a><a>Policies</a>
</nav>

<div class="abs hero" role="img" aria-label="Photo of a full classroom listening to an instructor"></div>
<div class="abs tagline">Classes! Try Keystone and you'll never go back to your old class!</div>

<section class="abs card green" style="left:44px">
  <h2>Welcome</h2>
  <p>Keystone Rescue Academy is Northern California's leader in CPR, BLS, and Basic First Aid Certifications! Taught by experienced Firefighters, our classes are much shorter and provide common sense knowledge and skills to each student to help prepare them for actual emergencies.</p>
  <span class="btn">READ MORE</span>
</section>
<section class="abs card" style="left:267px">
  <h2>About Us</h2>
  <p>We specializes in CPR and First Aid Certification Classes to businesses and individuals throughout Northern California. We provide these certifications two ways: ONSITE-We come to you, and HOSTED-we offer weekly classes</p>
  <span class="btn">READ MORE</span>
</section>
<section class="abs card" style="left:491px">
  <h2>Certification</h2>
  <p>Keystone Rescue Academy is Northern California's leader in CPR, BLS, and Basic First Aid Certifications! Taught by experienced Firefighters, our classes are much shorter and provide common sense knowledge and skills to each student to help prepare them for actual emergencies.</p>
  <span class="btn">READ MORE</span>
</section>

<section class="abs news">
  <h3>News Updates</h3>
  <div class="news-grid">
    <article class="post">
      <div class="ph" role="img" aria-label="Photo of medical staff in scrubs training at a bedside" style="background:linear-gradient(135deg,#8ea7c4,#d9d3cc)"></div>
      <h4>Lorem Ipsumroin gravida nibh vel</h4>
      <div class="date">27 January 2015</div>
      <p>Proin gravida nibh vel velit auctor aliquet sollicitudin, lorem quis bibendum auctor...</p>
    </article>
    <article class="post">
      <div class="ph" role="img" aria-label="Photo of a rescuer performing chest compressions outdoors" style="background:linear-gradient(180deg,#6f7f56,#9aa37a 60%,#5b6650)"></div>
      <h4>Lorem Ipsumroin gravida nibh vel</h4>
      <div class="date">27 January 2015</div>
      <p>Proin gravida nibh vel velit auctor aliquet sollicitudin, lorem quis bibendum auctor...</p>
    </article>
  </div>
</section>

<aside class="abs price" style="top:562px">
  <div class="t">CPR <b>$39</b></div>
  <div class="row"><span>Adult / Child / Infant</span><span>90 Minutes!</span></div>
  <span class="reg">REGISTER NOW</span>
</aside>
<aside class="abs price" style="top:680px">
  <div class="t">BLS <b>$49</b></div>
  <div class="row"><span>Healthcare/Dental</span><span style="margin-right:28px">90 Minutes!</span></div>
  <span class="reg">REGISTER NOW</span>
</aside>

<section class="abs reviews">
  <h3>Reviews</h3>
  <div class="stars">
    <svg width="74" height="14" viewBox="0 0 74 14"><g fill="#e8b923" stroke="#a07a10" stroke-width=".5"><path id="st" d="M7 0.5l1.9 4.3 4.6.4-3.5 3 1.1 4.5L7 10.3 2.9 12.7 4 8.2.5 5.2l4.6-.4z"/><use href="#st" x="15"/><use href="#st" x="30"/><use href="#st" x="45"/><use href="#st" x="60"/></g></svg>
  </div>
  <div class="who">Dorian M - CA, United States <span>26 Feb 2014</span></div>
  <p>I enjoyed the CPR class it was inexpensive and informative, in a short period of time.This is a demo version of Lorem Ipsum. Proin gravida nibh vel velit auctor aliquet. Aenean sollicitudin, lorem quis bibendum auctor, nisi elit consequat ipsum, nec sagittis sem nibh id elit.</p>
</section>

<div class="abs map" role="img" aria-label="Street map showing the academy location"></div>

<footer class="abs footer"></footer>
<div class="abs social"><span></span><span></span><span></span><span></span><span></span><span></span></div>
<div class="abs flinks">Home<i>|</i>Class Calender<i>|</i>Certification Classes<i>|</i>Classes for Groups<i>|</i>About Us<i>|</i>Policies<i>|</i>Medesto<i>|</i>Manteca<i>|</i>Tracy<i>|</i>Livermore</div>
<div class="abs copy">Copyright © 2014 Keystone Rescue Academy. All rights reserved.</div>
<div class="abs badge"></div>
</body>
</html>
```